Business card design needed

I need a business card design for a dog walking, dog minding and dog training business. Please refer to my website for the basic company colours and fonts I'm after. Planning on a double sided card, so all information doesn't need to be on the 'front' side.
Cheers

Industry/Entity Type

Dog Training

Contact Information for Business Card

Bramble Paws - gathering hounds
Rua 0498376214
bramblepaws.com.au
-walking
-holiday stays
-onsite care
-training and behavioural consultations

```html
<!DOCTYPE html>
<html lang="en">
<head>
<meta charset="utf-8">
<title>Bramble Paws – Business Card</title>
<link href="https://fonts.googleapis.com/css2?family=Rokkitt:wght@500;800&family=Didact+Gothic&family=Source+Code+Pro:wght@400&display=swap" rel="stylesheet">
<style>
  :root {
    --orange: #f15a27;
    --cream: #f0ebe5;
    --ink: #111111;
    --white: #ffffff;
    --silhouette: #c9c6c2;
    --dog-fur: #ece7e0;
    --dog-shade: #c9bfb2;
  }
  * { margin: 0; padding: 0; box-sizing: border-box; }
  html, body {
    width: 1200px; height: 900px; overflow: hidden;
    background: var(--white);
  }
  .card {
    position: absolute; left: 282px; width: 636px; height: 397px; overflow: hidden;
  }
  .card--front { top: 39px; background: var(--orange); }
  .card--back  { top: 465px; background: var(--cream); }

  .wordmark {
    position: absolute;
    font-family: "Rokkitt", serif; font-weight: 500;
    color: var(--white); white-space: nowrap; letter-spacing: 0.5px;
  }
  .tagline {
    position: absolute;
    font-family: "Didact Gothic", sans-serif;
    color: var(--white); white-space: nowrap;
  }
  .card--front .wordmark { left: 162px; top: 118px; font-size: 52px; line-height: 1; }
  .card--front .tagline  { left: 344px; top: 172px; font-size: 14px; }

  .website {
    position: absolute; left: 16px; top: 362px;
    font-family: "Didact Gothic", sans-serif; font-size: 14px; color: var(--white);
  }
  .dog-photo { position: absolute; }
  .card--front .dog-photo { left: 524px; top: 198px; width: 112px; height: 184px; }

  .header-band {
    position: absolute; left: 0; top: 33px; width: 636px; height: 115px; background: var(--orange);
  }
  .header-band .wordmark { left: 34px; top: 35px; font-size: 40px; line-height: 1; }
  .header-band .tagline  { left: 160px; top: 73px; font-size: 10px; }
  .header-band .dog-photo { left: 556px; top: 2px; width: 68px; height: 108px; }

  .walkers { position: absolute; left: 52px; top: 212px; width: 532px; height: 112px; }

  .contact {
    position: absolute; left: 22px; top: 158px; white-space: nowrap;
    font-family: "Didact Gothic", sans-serif; font-size: 39px; line-height: 1;
  }
  .contact__name { color: var(--orange); }
  .contact__phone { color: var(--ink); }

  .services { position: absolute; left: 343px; top: 168px; }
  .services__title {
    font-family: "Source Code Pro", monospace; font-size: 12.5px;
    color: var(--orange); letter-spacing: 0.5px;
  }
  .services__list {
    list-style: none; margin: 8px 0 0 34px;
    font-family: "Rokkitt", serif; font-weight: 800; font-size: 14px;
    line-height: 17px; color: var(--orange);
  }
  .credentials {
    position: absolute; left: 36px; top: 354px;
    font-family: "Didact Gothic", sans-serif; font-size: 11.5px; line-height: 16px;
    color: var(--ink);
  }
</style>
</head>
<body>

<section class="card card--front">
  <div class="wordmark">BRAMBLE PAWS</div>
  <div class="tagline">gathering hounds.</div>
  <div class="website">bramblepaws.com.au</div>
  <svg class="dog-photo" viewBox="0 0 112 184" role="img" aria-label="Photo of a small white fluffy dog sitting with its head raised">
    <defs>
      <linearGradient id="furFront" x1="0" y1="0" x2="0" y2="1">
        <stop offset="0" stop-color="var(--dog-shade)"/>
        <stop offset="1" stop-color="var(--dog-fur)"/>
      </linearGradient>
    </defs>
    <rect x="0" y="0" width="112" height="184" rx="40" fill="url(#furFront)"/>
  </svg>
</section>

<section class="card card--back">
  <div class="header-band">
    <div class="wordmark">BRAMBLE PAWS</div>
    <div class="tagline">gathering hounds.</div>
    <svg class="dog-photo" viewBox="0 0 68 108" role="img" aria-label="Photo of a small white fluffy dog sitting with its head raised">
      <defs>
        <linearGradient id="furBack" x1="0" y1="0" x2="0" y2="1">
          <stop offset="0" stop-color="var(--dog-shade)"/>
          <stop offset="1" stop-color="var(--dog-fur)"/>
        </linearGradient>
      </defs>
      <rect x="0" y="0" width="68" height="108" rx="24" fill="url(#furBack)"/>
    </svg>
  </div>

  <svg class="walkers" viewBox="0 0 532 112" role="img" aria-label="Faint grey silhouettes of a dog walker leading a pack of dogs">
    <defs>
      <linearGradient id="walkFade" x1="0" y1="0" x2="1" y2="0">
        <stop offset="0" stop-color="var(--silhouette)" stop-opacity="0.75"/>
        <stop offset="1" stop-color="var(--silhouette)" stop-opacity="0.5"/>
      </linearGradient>
    </defs>
    <rect x="0" y="0" width="532" height="112" rx="30" fill="url(#walkFade)"/>
  </svg>

  <div class="contact">
    <span class="contact__name">Rua</span>
    <span class="contact__phone">0498376214</span>
  </div>

  <div class="services">
    <div class="services__title">SERVICES:</div>
    <ul class="services__list">
      <li>Group dog walk</li>
      <li>Group dog walk casual</li>
      <li>Solo dog walk</li>
      <li>Solo dog walk casual</li>
      <li>On site, in home care</li>
      <li>Hound holiday stay</li>
    </ul>
  </div>

  <p class="credentials">*Bramble Paws is run by a qualified dog behaviourist and trainer who is also an accredited pet first aider.<br>We hold pet care specific public liability insurance and carry a current police check.</p>
</section>

</body>
</html>
```